Business Card for a Jewellery Brand

Business card for an upscale jewellery brand. Attached is the brand logo and icon and color board. I am looking for two card versions: one for the founder and one is generic. The card should be elegant and convey upscale and premium feel. I am open to both square and rectangle card shapes.

Industry/Entity Type

Jewelry

Contact Information for Business Card

Two cards: (1) Sunela Parvaniya (Founder) (2) General
(1) Sunela Parvaniya card should have Name: Sunela Parvaniya, Title: Founder Email id: sunela@quiremo.com.au. Phone no: +61452913307
(2) Generic card should have Email id: info@quiremo.com.au. Phone no: +61436207518

Requirements
Must have
• Workmark
• ICON
• Phone no
• Email ID
• ABN: 58219740312 (Note: ABN is Business number in Australia)
• Website: www.quiremo.com.au
• Instagram: quiremo_jewellery
• Facebook: @quiremojewellery
Nice to have
• Tagline

```html
<!DOCTYPE html>
<html lang="en">
<head>
<meta charset="UTF-8">
<title>Quiremo Business Card</title>
<link href="https://fonts.googleapis.com/css2?family=Jost:wght@300;400;500&display=swap" rel="stylesheet">
<style>
  :root {
    --stage: #2b2b2d;
    --rose: #e79b98;
    --rose-deep: #d98582;
    --paper: #ffffff;
    --ink: #5a5a5c;
  }
  * { box-sizing: border-box; margin: 0; padding: 0; }
  html, body {
    width: 1200px; height: 900px; overflow: hidden;
    background: var(--stage);
    font-family: "Jost", "Futura", sans-serif;
  }
  .stage {
    width: 1200px; height: 900px;
    display: flex; flex-direction: column;
    align-items: center; justify-content: center; gap: 30px;
  }
  .card {
    position: relative;
    width: 700px; height: 400px;
    overflow: hidden;
  }
  .card-front { background: var(--rose); }
  .card-back { background: var(--paper); }

  .wordmark {
    position: absolute; left: 60px; top: 200px;
    display: flex; align-items: center; gap: 16px;
    color: var(--paper);
    font-weight: 300; font-size: 40px; letter-spacing: 12px;
  }
  .wordmark-dot {
    width: 14px; height: 14px; border-radius: 50%;
    background: var(--paper);
  }
  .front-accent {
    position: absolute; right: 40px; top: 50px;
    width: 300px; height: 300px;
  }

  .abn {
    position: absolute; left: 44px; top: 38px;
    font-size: 15px; letter-spacing: 1px; color: var(--ink);
  }
  .label { color: var(--rose); margin-right: 6px; }

  .person { position: absolute; left: 44px; top: 218px; }
  .person-name {
    color: var(--rose); font-weight: 400;
    font-size: 21px; letter-spacing: 1.5px; text-transform: uppercase;
  }
  .person-title {
    color: var(--ink); font-weight: 500;
    font-size: 18px; letter-spacing: 1px; text-transform: uppercase;
  }
  .contacts {
    position: absolute; left: 44px; top: 296px;
    list-style: none; font-size: 17px; line-height: 27px;
    color: var(--ink); letter-spacing: 1px;
  }
  .socials {
    position: absolute; left: 320px; top: 323px;
    list-style: none; font-size: 17px; line-height: 27px;
    color: var(--ink); letter-spacing: 1px;
  }
  .back-accent {
    position: absolute; right: 34px; top: 60px;
    width: 220px; height: 220px;
  }
</style>
</head>
<body>
<main class="stage">
  <section class="card card-front" aria-label="Card front">
    <div class="wordmark"><span class="wordmark-dot"></span>QUIREMO</div>
    <svg class="front-accent" viewBox="0 0 300 300" aria-hidden="true">
      <circle cx="150" cy="150" r="130" fill="none" stroke="var(--rose-deep)" stroke-opacity="0.45" stroke-width="14"/>
    </svg>
  </section>

  <section class="card card-back" aria-label="Card back">
    <p class="abn"><span class="label">ABN:</span>58219740312</p>
    <div class="person">
      <p class="person-name">Sunela Parvaniya</p>
      <p class="person-title">Founder</p>
    </div>
    <ul class="contacts">
      <li><span class="label">p:</span>+61452913307</li>
      <li><span class="label">e:</span>sunela@quiremo.com.au</li>
      <li><span class="label">w:</span>www.quiremo.com.au</li>
    </ul>
    <ul class="socials">
      <li><span class="label">Fb:</span>quiremo_jewellery</li>
      <li><span class="label">Ins:</span>@quiremojewellery</li>
    </ul>
    <svg class="back-accent" viewBox="0 0 220 220" aria-hidden="true">
      <circle cx="110" cy="110" r="96" fill="none" stroke="var(--rose)" stroke-width="14"/>
    </svg>
  </section>
</main>
</body>
</html>
```